We need 5-10 Instagram posts for a restaurant located in Dubai, UAE.

Background about the restaurant:

Forks and fizz is a boutique burgers and comfort food joint located at Dubai, UAE. We started operations in September 2016. The main focus on our food is for it to be simple, original and freshly made. The majority of our orders are take away with fewer people opting for dinning in. We connect with our customers through our Instagram account & our customers rely on it for updates.

The brief

What we are looking for is a vector design (advertisement) for multiple purposes including:

1. announcing that we started delivery
2. a post that we can use multiple times during the year just as a "reminder that we deliver"
3. posts that serve as an advertisement

posts need to be as simple as possible

for reference, our Instagram account is @forksandfizz

Colors
f04a50
ffffff
000000

Requirements
Should not have
• the designs should not have too many colors

```html
<!DOCTYPE html>
<html lang="en">
<head>
<meta charset="utf-8">
<title>Delivery and cones posts</title>
<link rel="stylesheet" href="https://fonts.googleapis.com/css2?family=Quicksand:wght@700&display=swap">
<style>
  :root {
    --backdrop: #d8d8d8;
    --post-bg: #ffffff;
    --ink: #1c1c1c;
    --brand-red: #e8282c;
  }
  html, body {
    margin: 0;
    padding: 0;
    overflow: hidden;
  }
  .canvas {
    position: relative;
    width: 1200px;
    height: 1200px;
    background: var(--backdrop);
    overflow: hidden;
  }
  .post {
    position: absolute;
    top: 380px;
    width: 440px;
    height: 440px;
    background: var(--post-bg);
    box-shadow: 0 6px 18px rgba(0, 0, 0, 0.12);
  }
  .post--delivery { left: 120px; }
  .post--cones { left: 640px; }
  .post__art {
    position: absolute;
    display: block;
  }
  .post--delivery .post__art {
    left: 117px;
    top: 90px;
    width: 150px;
    height: 74px;
  }
  .post--cones .post__art {
    left: 191px;
    top: 58px;
    width: 70px;
    height: 126px;
  }
  .post__headline {
    position: absolute;
    left: 0;
    right: 0;
    margin: 0;
    text-align: center;
    font-family: "Quicksand", sans-serif;
    font-weight: 700;
    font-size: 60px;
    line-height: 60px;
    letter-spacing: 0.5px;
    color: var(--brand-red);
  }
  .post--delivery .post__headline { top: 198px; }
  .post--cones .post__headline { top: 200px; }
</style>
</head>
<body>
  <main class="canvas">
    <section class="post post--delivery">
      <svg class="post__art" viewBox="0 0 150 74" role="img" aria-label="Illustration of a burger moving fast with speed lines">
        <rect x="0" y="0" width="150" height="74" rx="16" fill="#1c1c1c"/>
      </svg>
      <h2 class="post__headline">we delivery<br>to you</h2>
    </section>
    <section class="post post--cones">
      <svg class="post__art" viewBox="0 0 70 126" role="img" aria-label="Illustration of fries served in a paper cone">
        <rect x="0" y="0" width="70" height="126" rx="10" fill="#1c1c1c"/>
      </svg>
      <h2 class="post__headline">we serve<br>in cones</h2>
    </section>
  </main>
</body>
</html>
```